Professional & attention grabbing.

A business card design, front and back. I already have a logo I will attach, but I am open to something new as well.
Things to include:
Name:
Title:
Phone:
Email:
Wanting something that is professional but attention grabbing.
Also we do a lot of work using drones on natural gas pipelines (leading the future)if you want to include any of that. I'm open to ideas.
Target Market(s)
Natural gas transmission industry / greenhouse gas mitigation industry
Industry/Entity Type
Business
Colors
Designer to choose colors to be used in the design.
Look and feel
Each slider illustrates characteristics of the customer's brand and the style your logo design should communicate.

```html
<!DOCTYPE html>
<html lang="en">
<head>
<meta charset="utf-8">
<title>KV Field Surveys – Business Card</title>
<link rel="stylesheet" href="https://fonts.googleapis.com/css2?family=Roboto:wght@300;400;700;900&display=swap">
<style>
  :root {
    --page-bg: #3a3431;
    --card-black: #141516;
    --card-edge: #1d1e20;
    --brand-red: #b8232a;
    --logo-grey: #c9c9c9;
    --text-white: #f2f2f2;
    --text-muted: #9a9a9a;
    --rule-grey: #8a8a8a;
  }
  * { margin: 0; padding: 0; box-sizing: border-box; }
  html, body {
    width: 1200px; height: 864px; overflow: hidden;
    background: var(--page-bg);
    font-family: "Roboto", Arial, sans-serif;
  }
  .stage {
    position: relative; width: 1200px; height: 864px;
  }
  .card {
    position: absolute;
    width: 525px; height: 300px;
    background: linear-gradient(160deg, var(--card-edge), var(--card-black));
    box-shadow: 0 14px 30px rgba(0,0,0,.45);
  }
  /* Front */
  .card--front { left: 50px; top: 282px; }
  .front-mark {
    position: absolute; left: 0; right: 0; top: 78px;
    display: flex; align-items: center; justify-content: center; gap: 14px;
  }
  .front-mark__square {
    width: 44px; height: 44px; background: var(--brand-red);
  }
  .front-mark__name {
    color: var(--logo-grey); font-weight: 900; font-size: 34px;
    letter-spacing: .5px; text-transform: uppercase; line-height: 1;
  }
  .front-web {
    position: absolute; left: 0; right: 0; top: 212px; text-align: center;
    color: var(--text-muted); font-size: 13px; letter-spacing: 5px; font-weight: 400;
  }
  /* Back */
  .card--back { left: 625px; top: 282px; }
  .brand {
    position: absolute; right: 34px; top: 88px;
    display: flex; align-items: center; gap: 10px;
  }
  .brand__square { width: 22px; height: 22px; background: var(--brand-red); }
  .brand__name {
    color: var(--text-white); font-weight: 900; font-size: 22px;
    text-transform: uppercase; line-height: 1;
  }
  .person { position: absolute; left: 28px; top: 92px; width: 108px; }
  .person__name {
    color: var(--brand-red); font-size: 15px; font-weight: 400;
    text-transform: uppercase; letter-spacing: .3px;
  }
  .person__title {
    color: var(--text-white); font-size: 13px; font-weight: 400;
    text-transform: uppercase; margin-top: 1px; padding-bottom: 5px;
    border-bottom: 1px solid var(--rule-grey);
  }
  .contacts {
    position: absolute; left: 28px; top: 148px; list-style: none;
  }
  .contacts li {
    display: flex; align-items: center; gap: 10px;
    color: var(--text-white); font-size: 12.5px; font-weight: 300;
    height: 20px;
  }
  .contacts svg { width: 11px; height: 11px; fill: var(--brand-red); flex: none; }
  .divider {
    position: absolute; left: 28px; right: 26px; top: 232px;
    height: 1px; background: var(--rule-grey);
  }
</style>
</head>
<body>
<main class="stage">
  <section class="card card--front" aria-label="Card front">
    <div class="front-mark">
      <span class="front-mark__square"></span>
      <span class="front-mark__name">KV Field Surveys</span>
    </div>
    <p class="front-web">www.kvfield.com</p>
  </section>

  <section class="card card--back" aria-label="Card back">
    <div class="person">
      <p class="person__name">Mark Ellison</p>
      <p class="person__title">President</p>
    </div>
    <ul class="contacts">
      <li>
        <svg viewBox="0 0 12 12" aria-hidden="true"><path d="M2.5 0.8l2 2.2-1 1.3c.7 1.5 1.9 2.7 3.4 3.4l1.3-1 2.2 2-1 2.3C5 10.8 1.2 7 .2 1.8z"/></svg>
        <span>555 0142 7781</span>
      </li>
      <li>
        <svg viewBox="0 0 12 12" aria-hidden="true"><path d="M0 2h12v1.2L6 7 0 3.2zM0 4.6l6 3.8 6-3.8V10H0z"/></svg>
        <span>mark@kvfield.com</span>
      </li>
      <li>
        <svg viewBox="0 0 12 12" aria-hidden="true"><path d="M6 0a4 4 0 0 1 4 4c0 3-4 8-4 8S2 7 2 4a4 4 0 0 1 4-4zm0 2.4A1.6 1.6 0 1 0 6 5.6 1.6 1.6 0 0 0 6 2.4z"/></svg>
        <span>www.kvfield.com</span>
      </li>
    </ul>
    <div class="divider"></div>
    <div class="brand">
      <span class="brand__square"></span>
      <span class="brand__name">KV Field Surveys</span>
    </div>
  </section>
</main>
</body>
</html>
```